sydney wedding photography business needs a business card design

we need a business card design for a sydney based wedding photography and videography business. our business name is :golden hour studio and film. our target clients are 24-35 yrs female. our style is candid, organic, natural, dynamic. we are a team of young photographers and videographers, and help brides to create memories that they will cherish for the rest of their lives. the logo will be provided. we want an elegant design that reflects our style, and also want to give a great impression to our clients that we are one of the best studios in sydney and our brand means quality and premium service.

Target Market(s)

bride to be, 24-35 years old, living in sydney and surrunding areas

Industry/Entity Type

Wedding Photography

Contact Information for Business Card

address: 57 tarrant street, glenmore nsw 2047
mobile: 0431872259
phone: (02) 9163 2408
info@tidewillowstudio.net.au
www.tidewillowstudio.net.au
facebook:tidewillowweddings
instagram:tidewillowweddings

Font styles to use
Serif
Sans Serif

Requirements
Nice to have
• maybe add my slogan"memories beyond eternity" if the layout looks good
Should not have
• no black color, not good idea for wedding biz card

```html
<!DOCTYPE html>
<html lang="en">
<head>
<meta charset="utf-8">
<title>Golden Hour Studio and Film – Business Card</title>
<link rel="stylesheet" href="https://fonts.googleapis.com/css2?family=Jost:wght@400;500&display=swap">
<style>
  :root {
    --backdrop: #e9e4da;
    --ink: #3a2a0a;
    --bronze-dark: #6e4f10;
    --bronze: #8a6516;
    --gold-light: #e3b526;
    --gold: #d1a01c;
    --gold-deep: #a87c12;
    --cream: #f7e9bd;
    --divider: #efdca0;
  }
  * { margin: 0; padding: 0; box-sizing: border-box; }
  html, body { width: 1200px; height: 950px; overflow: hidden; }
  body {
    background: var(--backdrop);
    font-family: "Jost", sans-serif;
    color: var(--ink);
    position: relative;
  }
  .card {
    position: absolute;
    width: 600px;
    height: 343px;
    border-radius: 4px;
    overflow: hidden;
    box-shadow: 0 12px 30px rgba(60,40,0,.22);
  }

  /* Front */
  .card-front { left: 80px; top: 110px; background: linear-gradient(100deg, var(--gold-deep), var(--gold) 45%, var(--gold-light)); }
  .front-band {
    height: 150px;
    background: linear-gradient(100deg, var(--bronze-dark), var(--bronze));
    border-bottom: 3px solid var(--divider);
    display: flex; align-items: center; justify-content: center;
  }
  .brand-name {
    font-weight: 500;
    font-size: 30px;
    letter-spacing: 1px;
    color: var(--cream);
  }
  .front-info {
    display: flex;
    gap: 34px;
    padding: 34px 34px 0;
    font-size: 15px;
    line-height: 1.55;
  }
  .contact-block { border-top: 1px solid var(--ink); padding-top: 12px; }
  .person-name { font-size: 20px; letter-spacing: 1px; text-transform: uppercase; line-height: 1.2; }
  .person-role { font-size: 12px; letter-spacing: 2px; text-transform: uppercase; margin-bottom: 10px; }
  .contact-line { display: flex; align-items: center; gap: 8px; white-space: nowrap; }
  .contact-line svg { width: 13px; height: 13px; flex: none; fill: var(--ink); }
  .contact-block.phones, .contact-block.web { padding-top: 16px; }

  /* Back */
  .card-back {
    left: 520px; top: 480px;
    background: radial-gradient(circle at 55% 40%, var(--gold-light), var(--gold) 55%, var(--gold-deep));
  }
  .back-brand { position: absolute; left: 36px; bottom: 36px; }
  .back-brand .brand-name { color: var(--ink); font-size: 26px; display: flex; align-items: center; gap: 12px; }
  .brand-dot { width: 14px; height: 14px; border-radius: 50%; background: var(--ink); }
  .social-line { display: flex; align-items: center; gap: 6px; font-size: 15px; margin-top: 6px; }
  .social-dot { width: 12px; height: 12px; border-radius: 50%; background: var(--ink); }
</style>
</head>
<body>

<section class="card card-front" aria-label="Business card front">
  <div class="front-band">
    <span class="brand-name">Golden Hour Studio and Film</span>
  </div>
  <div class="front-info">
    <div class="contact-block person">
      <p class="person-name">Liam Harper</p>
      <p class="person-role">Photographer</p>
      <p>57 tarrant street</p>
      <p>glenmore nsw 2047</p>
    </div>
    <div class="contact-block phones">
      <p class="contact-line">
        <svg viewBox="0 0 24 24"><path d="M6.6 10.8a15 15 0 0 0 6.6 6.6l2.2-2.2c.3-.3.7-.4 1-.2 1.1.4 2.3.6 3.6.6.6 0 1 .4 1 1V20c0 .6-.4 1-1 1A17 17 0 0 1 3 4c0-.6.4-1 1-1h3.5c.6 0 1 .4 1 1 0 1.3.2 2.5.6 3.6.1.3 0 .7-.2 1z"/></svg>
        (02) 9163 2408</p>
      <p class="contact-line">
        <svg viewBox="0 0 24 24"><path d="M7 1h10a2 2 0 0 1 2 2v18a2 2 0 0 1-2 2H7a2 2 0 0 1-2-2V3a2 2 0 0 1 2-2zm0 3v14h10V4z"/></svg>
        0431 872 259</p>
    </div>
    <div class="contact-block web">
      <p class="contact-line">
        <svg viewBox="0 0 24 24"><path d="M2 5h20v14H2zm2 2v.5l8 5 8-5V7z"/></svg>
        info@tidewillowstudio.net.au</p>
      <p class="contact-line">
        <svg viewBox="0 0 24 24"><circle cx="12" cy="12" r="10"/></svg>
        www.tidewillowstudio.net.au</p>
    </div>
  </div>
</section>

<section class="card card-back" aria-label="Business card back">
  <div class="back-brand">
    <p class="brand-name"><span class="brand-dot"></span>Golden Hour Studio and Film</p>
    <p class="social-line"><span class="social-dot"></span><span class="social-dot"></span>tidewillowweddings</p>
  </div>
</section>

</body>
</html>
```